Moravel Aesthetic Doctor

I require an elegant, luxurious looking business card for my aesthetic business. I am a doctor and that will set me aside from competitors. I am planning to provide home and spa based treatments to clients with high expectations. I have attached my logo.

```html
<!DOCTYPE html>
<html lang="en">
<head>
<meta charset="utf-8">
<title>Moravel Aesthetic Doctor – Business Card</title>
<link rel="stylesheet" href="https://fonts.googleapis.com/css2?family=Roboto:wght@300;400&family=Rajdhani:wght@600&family=Montserrat:wght@400&display=swap">
<style>
  :root {
    --backdrop: #cfcfd1;
    --card: #f3f3f4;
    --card-shade: #e6e6e8;
    --ink: #2c2c2e;
    --brand-grey: #8a8d96;
    --brand-blue: #3f9bd6;
    --band-deep: #1c6fb5;
    --band-light: #4aa3dc;
    --panel-top: #4eaadf;
    --panel-bottom: #2378bd;
    --divider: #9aa0aa;
    --white: #ffffff;
  }
  * { margin: 0; padding: 0; box-sizing: border-box; }
  html, body { width: 1200px; height: 576px; overflow: hidden; }
  body { background: var(--backdrop); position: relative; font-family: "Roboto", sans-serif; }

  .card {
    position: absolute; top: 139px; width: 484px; height: 294px;
    border-radius: 14px; overflow: hidden;
    background: linear-gradient(180deg, var(--card), var(--card-shade));
    box-shadow: 0 3px 8px rgba(0,0,0,0.22);
  }
  .card--front { left: 81px; }
  .card--back { left: 602px; }

  .brand-mark {
    position: absolute; border-radius: 50%;
    border: 2px solid var(--brand-grey);
  }
  .brand-name {
    position: absolute; font-family: "Roboto", sans-serif; font-weight: 300;
    color: var(--brand-grey); line-height: 1; text-transform: uppercase;
  }
  .brand-name span { display: block; }

  .card--front .brand-mark { left: 72px; top: 58px; width: 96px; height: 96px; }
  .card--front .brand-name { left: 190px; top: 70px; }
  .card--front .brand-name .brand-name__main { font-size: 46px; letter-spacing: 3px; }
  .card--front .brand-name .brand-name__sub { font-size: 20px; letter-spacing: 2px; margin-top: 6px; }

  .services {
    position: absolute; left: 0; right: 0; top: 196px;
    text-align: center; font-size: 13.5px; color: var(--ink); line-height: 19px;
  }
  .services .sep { color: var(--brand-blue); margin: 0 7px; }

  .tagline-band {
    position: absolute; left: 0; right: 0; top: 240px; height: 32px;
    background: linear-gradient(90deg, var(--band-deep), var(--band-light) 60%, var(--band-deep));
    color: var(--white); font-family: "Montserrat", sans-serif; font-size: 13px;
    letter-spacing: 1px; display: flex; align-items: center; justify-content: center;
  }

  .card--back .brand-mark { left: 70px; top: 70px; width: 80px; height: 80px; }
  .card--back .brand-name { left: 0; width: 220px; text-align: center; top: 170px; }
  .card--back .brand-name .brand-name__main { font-size: 38px; letter-spacing: 2px; }
  .card--back .brand-name .brand-name__sub { font-size: 15px; letter-spacing: 1.5px; margin-top: 5px; }

  .contact-panel { position: absolute; inset: 0; }

  .contact { position: absolute; left: 281px; top: 72px; color: var(--white); }
  .contact__name { font-family: "Rajdhani", sans-serif; font-weight: 600; font-size: 18px; line-height: 20px; }
  .contact__creds { font-family: "Roboto", sans-serif; font-weight: 400; font-size: 10px; margin-left: 3px; }
  .contact__title { font-size: 12.5px; line-height: 16px; margin-top: 3px; }
  .contact__list { list-style: none; margin-top: 14px; }
  .contact__list li { display: flex; align-items: center; font-size: 12.5px; height: 18.5px; }
  .contact__list svg { width: 10px; height: 10px; margin-right: 9px; fill: var(--white); }
  .contact__follow { display: flex; align-items: center; font-size: 12.5px; margin-top: 5px; }
  .social-dot { width: 11px; height: 11px; border-radius: 50%; background: var(--white); margin-left: 5px; }
  .social-dot:first-child { margin-left: 7px; }
</style>
</head>
<body>

<section class="card card--front" aria-label="Card front">
  <div class="brand-mark"></div>
  <div class="brand-name">
    <span class="brand-name__main">Moravel</span>
    <span class="brand-name__sub">Aesthetic Doctor</span>
  </div>
  <div class="services">
    <div>Dermal Injectables<span class="sep">|</span>Plasma Facials<span class="sep">|</span>Microneedling</div>
    <div>Skin Boosters<span class="sep">|</span>Excessive Sweating</div>
  </div>
  <div class="tagline-band">HOME AND SPA BASED TREATMENTS</div>
</section>

<section class="card card--back" aria-label="Card back">
  <svg class="contact-panel" width="484" height="294" viewBox="0 0 484 294">
    <defs>
      <linearGradient id="panelFill" x1="0" y1="0" x2="0.3" y2="1">
        <stop offset="0" stop-color="var(--panel-top)"/>
        <stop offset="1" stop-color="var(--panel-bottom)"/>
      </linearGradient>
    </defs>
    <path d="M214 0 Q262 147 218 294 L484 294 L484 0 Z" fill="url(#panelFill)"/>
    <path d="M214 0 Q262 147 218 294" fill="none" stroke="var(--divider)" stroke-width="6"/>
  </svg>

  <div class="brand-mark"></div>
  <div class="brand-name">
    <span class="brand-name__main">Moravel</span>
    <span class="brand-name__sub">Aesthetic Doctor</span>
  </div>

  <div class="contact">
    <div class="contact__name">Dr Liesel Varno<span class="contact__creds">MRCPCH MD</span></div>
    <div class="contact__title">Australasian Diploma<br>of Aesthetic Medicine</div>
    <ul class="contact__list">
      <li><svg viewBox="0 0 10 10"><path d="M2 0.5 L3.6 2.6 L2.8 3.6 Q4 6 6.4 7.2 L7.4 6.4 L9.5 8 L8.4 9.5 Q3.5 9 0.5 1.6 Z"/></svg>0800 555 014</li>
      <li><svg viewBox="0 0 10 10"><path d="M0 2 H10 V8.5 H0 Z M0.8 2.6 L5 5.6 L9.2 2.6" stroke="var(--panel-bottom)" stroke-width="0.8"/></svg>liesel@moravel.co.nz</li>
      <li><svg viewBox="0 0 10 10"><circle cx="5" cy="5" r="4.4" fill="none" stroke="var(--white)" stroke-width="1"/><ellipse cx="5" cy="5" rx="1.8" ry="4.4" fill="none" stroke="var(--white)" stroke-width="0.9"/><path d="M0.6 5 H9.4" stroke="var(--white)" stroke-width="0.9"/></svg>www.moravel.co.nz</li>
    </ul>
    <div class="contact__follow">Follow us on:<span class="social-dot"></span><span class="social-dot"></span></div>
  </div>
</section>

</body>
</html>
```